Natural Medicine & Health/Fitness Coaching studio requires web page

Require a innovative web page for a studio that coaches clients to better health, nutrition and fitness. The studio compromises of Clinical Nutritionists, Naturopaths, Rehab Trainers, Personal Trainers and Sport Coaches. Would like to see earthy but bold designs emphasizing nutritional health and athletic performance.
Updates

Design only launched today.

Target Market(s)

All genders from 20's to 60's, as well as families

Industry/Entity Type

Nutritionist

Coding

Coded - Design and coding required

Number of Pages Required

3 page

Colors
abd037
3277b5
fbee3d
fece3e
33b8a4
f04a50

Requirements
Must have
• Online booking system, ability to message
• Home page
• Coaching/Fitness page
• Nutritional Medicine page
• Must be suitable for both Fitness and Nutrition

```html
<!DOCTYPE html>
<html lang="en">
<head>
<meta charset="utf-8">
<title>Verdant Core Wellness</title>
<link href="https://fonts.googleapis.com/css2?family=Crimson+Text:wght@400;600;700&family=Roboto:wght@400;500;700&display=swap" rel="stylesheet">
<style>
:root{
  --green:#7cb932;
  --green-light:#abd037;
  --blue:#1f4f91;
  --blue-bright:#3277b5;
  --yellow:#fece3e;
  --teal:#33b8a4;
  --red:#f04a50;
  --ink:#1c1c1c;
  --muted:#8a8a8a;
  --black:#080808;
  --white:#ffffff;
}
*{box-sizing:border-box;margin:0;padding:0}
html,body{width:1200px;height:4627px;overflow:hidden;background:var(--white)}
body{position:relative;font-family:"Roboto",sans-serif;color:var(--ink)}
.abs{position:absolute}
.serif{font-family:"Crimson Text",serif}

/* header */
.topbar{position:absolute;top:0;left:755px;display:flex}
.topbar a{display:block;height:32px;line-height:32px;padding:0 40px;font-size:13px;font-weight:700;color:#fff;text-decoration:none;letter-spacing:.5px}
.topbar .contact{background:var(--green);border-radius:0 0 0 20px}
.topbar .book{background:var(--blue);border-radius:0 0 20px 0}
.logo{position:absolute;left:114px;top:38px;display:flex;align-items:center;gap:10px}
.logo .dot{width:26px;height:26px;border-radius:50%;background:var(--green)}
.logo span{font-family:"Crimson Text",serif;font-size:40px;font-weight:700;color:var(--green);line-height:1}
.nav{position:absolute;top:76px;right:114px;display:flex;gap:30px}
.nav a{font-size:14px;font-weight:500;color:var(--ink);text-decoration:none}

/* hero */
.hero{position:absolute;top:140px;left:0;width:1200px;height:650px;background:linear-gradient(110deg,#2a2a2a 0%,#5a5a5a 45%,#8c8c8c 70%,#3a3a3a 100%)}
.hero h1{position:absolute;left:111px;top:120px;font-family:"Crimson Text",serif;font-weight:400;font-size:64px;line-height:62px;color:#fff;letter-spacing:1px}
.hero p{position:absolute;left:114px;top:250px;width:560px;font-size:20px;line-height:30px;color:#fff}
.btn-green{position:absolute;display:block;background:var(--green);color:#fff;font-weight:700;font-size:15px;text-decoration:none;border-radius:24px;text-align:center}
.hero .btn-green{left:114px;top:354px;width:170px;height:46px;line-height:46px}
.hero svg{position:absolute;left:0;bottom:-2px}

/* services */
.section-title{position:absolute;left:0;width:1200px;text-align:center;font-family:"Crimson Text",serif;font-weight:600;color:var(--ink)}
.svc-img{position:absolute;width:457px;height:247px;border:3px solid #fff;box-shadow:0 0 0 1px #ddd}
.tag{position:absolute;height:46px;line-height:46px;padding:0 22px;font-family:"Crimson Text",serif;font-weight:700;font-size:23px;color:#fff;white-space:nowrap}
.tag.r{border-radius:0 23px 23px 0}
.tag.l{border-radius:23px 0 0 23px}
.svc-title{position:absolute;font-family:"Crimson Text",serif;font-size:40px;color:var(--ink)}
.svc-text{position:absolute;width:430px;font-size:13.5px;line-height:26px;color:var(--muted)}
.btn-out{position:absolute;width:168px;height:42px;line-height:40px;border:1px solid #ccc;text-align:center;font-size:14px;font-weight:700;color:var(--red);text-decoration:none}

/* journey */
.journey{position:absolute;left:0;top:2668px;width:1200px;height:494px;background:var(--green)}
.journey h2{position:absolute;top:135px;width:1200px;text-align:center;font-family:"Crimson Text",serif;font-weight:700;font-size:46px;color:#fff}
.journey p{position:absolute;top:212px;width:1200px;text-align:center;font-size:14px;color:#fff}
.features{position:absolute;top:282px;left:0;width:1200px;display:flex;justify-content:center;gap:70px}
.features div{display:flex;align-items:center;gap:14px;font-size:26px;font-weight:500;color:#fff}
.video{position:absolute;left:265px;top:3060px;width:670px;height:349px;background:linear-gradient(120deg,#b9a79a,#7d6f6a 50%,#d2c4bb);border:3px solid #fff;box-shadow:0 2px 10px rgba(0,0,0,.2)}
.play{position:absolute;left:50%;top:50%;width:76px;height:76px;margin:-38px 0 0 -38px;border-radius:50%;background:rgba(255,255,255,.9)}

/* blog */
.rule{position:absolute;left:114px;top:3508px;width:972px;height:1px;background:#ddd}
.blog-img{position:absolute;width:269px;height:158px}
.blog-title{position:absolute;font-size:17px;font-weight:700;color:var(--ink)}
.meta{position:absolute;font-size:12.5px;color:#666}
.meta b{color:var(--green);font-weight:700}
.blog-text{position:absolute;width:260px;font-size:12.5px;line-height:20px;color:var(--muted)}
.side-img{position:absolute;left:728px;width:99px;height:77px}
.side-title{position:absolute;left:850px;width:240px;font-size:15px;font-weight:700;line-height:22px;color:var(--blue)}
.side-meta{position:absolute;left:850px;font-size:11px;color:#777}

/* footer */
.footer{position:absolute;left:0;top:4165px;width:1200px;height:462px;background:var(--black);color:#fff}
.footer h4{position:absolute;top:88px;font-size:17px;font-weight:700;letter-spacing:.3px}
.field{position:absolute;border:1px solid #777;font-size:13px;color:#ddd;padding:0 14px;line-height:38px;height:40px}
.submit{position:absolute;left:114px;top:277px;width:148px;height:38px;line-height:38px;background:var(--green);color:#fff;font-weight:700;font-size:14px;text-align:center}
.links{position:absolute;left:617px;top:140px;list-style:none}
.links li{font-size:13px;line-height:30px;color:#ddd}
.links li::before{content:"›";display:inline-block;width:22px;color:#fff}
.contact-row{position:absolute;left:796px;display:flex;gap:22px;font-size:13px;line-height:20px;color:#ddd}
.contact-row .ic{width:34px;height:34px;border-radius:50%;background:#2a2a2a;flex:none}
.frule{position:absolute;left:114px;top:357px;width:972px;height:1px;background:#444}
.copy{position:absolute;left:114px;top:400px;font-size:13px;color:#ccc}
.social{position:absolute;left:925px;top:390px;display:flex;gap:10px}
.social span{width:36px;height:36px;border:2px solid #fff;border-radius:50%}
</style>
</head>
<body>

<header>
  <div class="topbar"><a class="contact" href="#">CONTACT US</a><a class="book" href="#">BOOK NOW</a></div>
  <div class="logo"><i class="dot"></i><span>Verdant Core</span></div>
  <nav class="nav"><a href="#">HOME</a><a href="#">ABOUT US</a><a href="#">COACHING</a><a href="#">FITNESS</a><a href="#">NUTRITION</a><a href="#">CONTACT US</a></nav>
</header>

<section class="hero">
  <div class="abs" role="img" aria-label="Woman training on an exercise bike in a gym" style="inset:0"></div>
  <h1>HEALTH<br>NUTRITIONAL</h1>
  <p>Lorem ipsum dolor sit amet consectetur adipiscing elit sed do eiusmod tempor incididunt...</p>
  <a class="btn-green" href="#">READ MORE &#10140;</a>
  <svg width="1200" height="120" viewBox="0 0 1200 120" aria-hidden="true">
    <path d="M0 70 C250 120 500 120 750 70 C950 30 1100 10 1200 30 L1200 120 L0 120Z" fill="#fff"/>
    <path d="M0 50 C250 105 520 110 760 58 C950 18 1100 0 1200 10 L1200 30 C1100 12 950 30 760 72 C520 122 250 118 0 70Z" fill="var(--blue)"/>
    <path d="M0 35 C250 95 520 100 760 45 C950 5 1100 -8 1200 0 L1200 12 C1100 2 950 20 760 58 C520 110 250 105 0 50Z" fill="var(--green)"/>
  </svg>
</section>

<main>
  <h2 class="section-title" style="top:868px;font-size:48px">WHAT WE DO</h2>

  <!-- Clinical Nutritionists -->
  <div class="svc-img" role="img" aria-label="Fresh fruit and juice with a clinician" style="left:111px;top:987px;background:linear-gradient(135deg,#c94a3a,#e9e2d6 45%,#8cb34a)"></div>
  <div class="tag r" style="left:400px;top:1148px;background:var(--green)">Clinical Coaches</div>
  <h3 class="svc-title" style="left:660px;top:975px">Clinical Nutritionists</h3>
  <p class="svc-text" style="left:660px;top:1045px">Lorem ipsum dolor sit amet, consectetur adipiscing elit, sed do eiusmod tempor incididunt ut labore et dolore magna aliqua. Ut enim ad minim veniam, quis nostrud exercitation ullamco laboris nisi ut aliquip ex ea commodo consequat.</p>
  <a class="btn-out" href="#" style="left:660px;top:1193px">READ MORE &#10140;</a>

  <!-- Naturopaths -->
  <h3 class="svc-title" style="left:111px;top:1305px">Naturopaths</h3>
  <p class="svc-text" style="left:111px;top:1375px">Lorem ipsum dolor sit amet, consectetur adipiscing elit, sed do eiusmod tempor incididunt ut labore et dolore magna aliqua. Ut enim ad minim veniam, quis nostrud exercitation ullamco laboris nisi ut aliquip ex ea commodo consequat.</p>
  <a class="btn-out" href="#" style="left:111px;top:1520px">READ MORE &#10140;</a>
  <div class="svc-img" role="img" aria-label="Herbal capsules and fresh leaves" style="left:632px;top:1317px;background:linear-gradient(135deg,#4d6b2a,#b98a55 50%,#7a4a25)"></div>
  <div class="tag l" style="left:580px;top:1478px;background:var(--blue)">Naturopath Coach</div>

  <!-- Rehab Trainer -->
  <div class="svc-img" role="img" aria-label="Group rehabilitation exercise class" style="left:111px;top:1640px;background:linear-gradient(135deg,#d7dbe0,#9aa6b2 50%,#e8e4de)"></div>
  <div class="tag r" style="left:400px;top:1810px;background:var(--yellow)">Rehab Trainer</div>
  <h3 class="svc-title" style="left:660px;top:1630px">Rehab Trainer</h3>
  <p class="svc-text" style="left:660px;top:1700px">Lorem ipsum dolor sit amet, consectetur adipiscing elit, sed do eiusmod tempor incididunt ut labore et dolore magna aliqua. Ut enim ad minim veniam, quis nostrud exercitation ullamco laboris nisi ut aliquip ex ea commodo consequat.</p>
  <a class="btn-out" href="#" style="left:660px;top:1848px">READ MORE &#10140;</a>

  <!-- Personal Trainers -->
  <h3 class="svc-title" style="left:111px;top:1958px">Personal Trainers</h3>
  <p class="svc-text" style="left:111px;top:2028px">Lorem ipsum dolor sit amet, consectetur adipiscing elit, sed do eiusmod tempor incididunt ut labore et dolore magna aliqua. Ut enim ad minim veniam, quis nostrud exercitation ullamco laboris nisi ut aliquip ex ea commodo consequat.</p>
  <a class="btn-out" href="#" style="left:111px;top:2178px">READ MORE &#10140;</a>
  <div class="svc-img" role="img" aria-label="Personal trainer guiding a senior client through stretches" style="left:632px;top:1970px;background:linear-gradient(135deg,#b9c3c9,#8f9a6e 50%,#d6d0c4)"></div>
  <div class="tag l" style="left:580px;top:2136px;background:var(--teal)">Personal Trainers</div>

  <!-- Sport Coaches -->
  <div class="svc-img" role="img" aria-label="Coach spotting an athlete on gym equipment" style="left:111px;top:2298px;background:linear-gradient(135deg,#3a3a3a,#8a7570 50%,#c9b8b0)"></div>
  <div class="tag r" style="left:400px;top:2460px;background:var(--red)">Sport Coaches</div>
  <h3 class="svc-title" style="left:660px;top:2285px">Sport Coaches</h3>
  <p class="svc-text" style="left:660px;top:2355px">Lorem ipsum dolor sit amet, consectetur adipiscing elit, sed do eiusmod tempor incididunt ut labore et dolore magna aliqua. Ut enim ad minim veniam, quis nostrud exercitation ullamco laboris nisi ut aliquip ex ea commodo consequat.</p>
  <a class="btn-out" href="#" style="left:660px;top:2505px">READ MORE &#10140;</a>

  <!-- Journey -->
  <svg class="abs" style="left:0;top:2660px" width="1200" height="60" viewBox="0 0 1200 60" aria-hidden="true">
    <path d="M0 20 C300 -10 600 50 900 20 C1050 5 1150 5 1200 15 L1200 60 L0 60Z" fill="var(--green)"/>
  </svg>
  <section class="journey" style="border-radius:0">
    <h2>Start Your Health Journey With Us</h2>
    <p>Lorem ipsum dolor sit amet, consectetur adipiscing sed do eiusmod tempor.</p>
    <div class="features">
      <div><svg width="44" height="40" viewBox="0 0 44 40" aria-hidden="true"><path d="M22 36 C8 26 2 18 6 10 C10 3 18 4 22 11 C26 4 34 3 38 10 C42 18 36 26 22 36Z" fill="#fff"/></svg>Better Health</div>
      <div><svg width="40" height="40" viewBox="0 0 40 40" aria-hidden="true"><circle cx="20" cy="23" r="14" fill="#fff"/><path d="M20 9 C22 4 26 2 30 3 C28 7 24 9 20 9Z" fill="#fff"/></svg>Nutrition</div>
      <div><svg width="44" height="40" viewBox="0 0 44 40" aria-hidden="true"><rect x="4" y="12" width="6" height="16" fill="#fff"/><rect x="34" y="12" width="6" height="16" fill="#fff"/><rect x="10" y="17" width="24" height="6" fill="#fff"/><rect x="0" y="16" width="4" height="8" fill="#fff"/><rect x="40" y="16" width="4" height="8" fill="#fff"/></svg>Fitness Coach</div>
    </div>
  </section>
  <div class="video" role="img" aria-label="Video of a group fitness class celebrating together">
    <div class="play"><svg width="76" height="76" viewBox="0 0 76 76" aria-hidden="true"><path d="M31 24 L54 38 L31 52Z" fill="var(--red)"/></svg></div>
  </div>

  <!-- Blog -->
  <div class="rule"></div>
  <h2 class="section-title" style="top:3578px;font-size:44px">Latest Blogs &amp; News</h2>

  <div class="blog-img" role="img" aria-label="Healthy foods laid out on a table" style="left:114px;top:3677px;background:linear-gradient(135deg,#b5533c,#d9b48a 50%,#6e8a3a)"></div>
  <h3 class="blog-title" style="left:114px;top:3862px">REPEAT PREDEFINED CHUNKS</h3>
  <div class="meta" style="left:114px;top:3898px"><b>&#9679;</b> By Daniel, &nbsp; <b>&#9632;</b> 08 Jan 19</div>
  <p class="blog-text" style="left:114px;top:3930px">Sed ut perspiciatis unde iste natus error sit voluptatem accusantium...</p>

  <div class="blog-img" role="img" aria-label="Family running in a field at sunset" style="left:423px;top:3677px;background:linear-gradient(180deg,#e9b46a,#c98a45 55%,#6f7a3a)"></div>
  <h3 class="blog-title" style="left:423px;top:3862px">REPEAT PREDEFINED CHUNKS</h3>
  <div class="meta" style="left:423px;top:3898px"><b>&#9679;</b> By Daniel, &nbsp; <b>&#9632;</b> 08 Jan 19</div>
  <p class="blog-text" style="left:423px;top:3930px">Sed ut perspiciatis unde iste natus error sit voluptatem accusantium...</p>

  <div class="side-img" role="img" aria-label="Runners outdoors" style="top:3680px;background:linear-gradient(135deg,#7d9a5a,#cfc3a8)"></div>
  <h4 class="side-title" style="top:3676px">LOREM IPSUM IS NOT IN SIMPLY RANDOM TEXT</h4>
  <div class="side-meta" style="top:3728px"><b style="color:var(--green)">&#9632;</b> 18 Jan 2019, Health</div>

  <div class="side-img" role="img" aria-label="Family walking together" style="top:3788px;background:linear-gradient(135deg,#5a5a5a,#b7aca0)"></div>
  <h4 class="side-title" style="top:3784px">LOREM IPSUM IS NOT IN SIMPLY RANDOM TEXT</h4>
  <div class="side-meta" style="top:3836px"><b style="color:var(--green)">&#9632;</b> 18 Jan 2019, Fitness</div>

  <div class="side-img" role="img" aria-label="Bowl of fresh vegetables" style="top:3902px;background:linear-gradient(135deg,#c0452e,#e3a23a 50%,#5f8a30)"></div>
  <h4 class="side-title" style="top:3898px">LOREM IPSUM IS NOT IN SIMPLY RANDOM TEXT</h4>
  <div class="side-meta" style="top:3950px"><b style="color:var(--green)">&#9632;</b> 18 Jan 2019, Nutrition</div>
</main>

<svg class="abs" style="left:0;top:4060px" width="1200" height="110" viewBox="0 0 1200 110" aria-hidden="true">
  <path d="M0 60 C300 110 600 100 850 50 C1000 20 1120 10 1200 20 L1200 110 L0 110Z" fill="var(--black)"/>
  <path d="M0 40 C300 95 600 88 850 36 C1000 6 1120 -2 1200 4 L1200 20 C1120 10 1000 20 850 50 C600 100 300 110 0 60Z" fill="var(--blue)"/>
  <path d="M0 22 C300 80 600 74 850 22 C1000 -6 1120 -10 1200 -8 L1200 4 C1120 -2 1000 6 850 36 C600 88 300 95 0 40Z" fill="var(--green)"/>
</svg>

<footer class="footer">
  <h4 style="left:114px">CONTACT FORM</h4>
  <div class="field" style="left:114px;top:141px;width:208px">Name</div>
  <div class="field" style="left:334px;top:141px;width:208px">Email</div>
  <div class="field" style="left:114px;top:194px;width:428px;height:72px">Message</div>
  <div class="submit">SUBMIT</div>

  <h4 style="left:617px">QUICK LINKS</h4>
  <ul class="links"><li>Home</li><li>About Us</li><li>Coaching</li><li>Fitness</li><li>Nutrition</li><li>Contact Us</li></ul>

  <h4 style="left:796px">CONTACT DETAILS</h4>
  <div class="contact-row" style="top:132px"><span class="ic"></span><span>48 Fernleaf Lane, Brookvale,<br>Westmere</span></div>
  <div class="contact-row" style="top:196px;align-items:center"><span class="ic"></span><span>+61 400 123 456</span></div>
  <div class="contact-row" style="top:250px;align-items:center"><span class="ic"></span><span>hello@verdantcorewellness.com</span></div>

  <div class="frule"></div>
  <p class="copy">Copyrights &copy; 2019 Verdant Core Wellness. All Rights Reserved &nbsp;| &nbsp; Privacy Policy.</p>
  <div class="social"><span></span><span></span><span></span><span></span></div>
</footer>

</body>
</html>
```